Professional & attention grabbing.

A business card design, front and back. I already have a logo I will attach, but I am open to something new as well.
Things to include:
Name:
Title:
Phone:
Email:
Wanting something that is professional but attention grabbing.
Also we do a lot of work using drones on natural gas pipelines (leading the future)if you want to include any of that. I'm open to ideas.
Target Market(s)
Natural gas transmission industry / greenhouse gas mitigation industry
Industry/Entity Type
Business
Colors
Designer to choose colors to be used in the design.
Look and feel
Each slider illustrates characteristics of the customer's brand and the style your logo design should communicate.

```html
<!DOCTYPE html>
<html lang="en">
<head>
<meta charset="utf-8">
<title>Varen Inspections – Business Card</title>
<link href="https://fonts.googleapis.com/css2?family=Open+Sans:wght@400;600;700&display=swap" rel="stylesheet">
<style>
  :root {
    --backdrop: #b5b5b5;
    --card-light: #f2f2f2;
    --card-dark: #38383a;
    --ink: #3a3a3c;
    --accent: #be1e24;
    --white: #ffffff;
  }
  * { margin: 0; padding: 0; box-sizing: border-box; }
  html, body { width: 1200px; height: 900px; overflow: hidden; }
  body {
    background: var(--backdrop);
    font-family: "Open Sans", Arial, sans-serif;
    position: relative;
  }
  .card {
    position: absolute;
    top: 170px;
    width: 347px;
    height: 561px;
  }
  .card--front { left: 259px; background: var(--card-light); color: var(--ink); }
  .card--back { left: 631px; background: var(--card-dark); color: var(--white); }

  .brand {
    position: absolute;
    top: 134px;
    left: 0; right: 0;
    display: flex;
    align-items: center;
    justify-content: center;
    gap: 12px;
  }
  .brand__mark { width: 40px; height: 40px; background: var(--accent); }
  .brand__name {
    font-weight: 700;
    font-size: 25px;
    letter-spacing: 0.5px;
    color: var(--ink);
    text-transform: uppercase;
  }

  .contact {
    position: absolute;
    top: 394px;
    left: 0; right: 0;
    text-align: center;
  }
  .contact__name { font-size: 21px; font-weight: 600; line-height: 1.2; text-transform: uppercase; }
  .contact__first { color: var(--accent); }
  .contact__title { font-size: 14.5px; margin-top: 4px; }
  .contact__details { margin-top: 20px; font-size: 14.5px; line-height: 21px; }
  .contact__label { color: var(--accent); font-weight: 700; }

  .back-brand {
    position: absolute;
    top: 193px;
    left: 0; right: 0;
    display: flex;
    flex-direction: column;
    align-items: center;
    gap: 18px;
  }
  .back-brand__mark { width: 110px; height: 110px; background: var(--accent); }
  .back-brand__name {
    font-weight: 700;
    font-size: 22px;
    letter-spacing: 0.5px;
    text-transform: uppercase;
    color: var(--white);
  }
  .website {
    position: absolute;
    top: 492px;
    left: 0; right: 0;
    text-align: center;
    font-size: 15px;
    font-weight: 600;
  }
</style>
</head>
<body>
  <section class="card card--front">
    <div class="brand">
      <span class="brand__mark"></span>
      <span class="brand__name">Varen Inspections</span>
    </div>
    <div class="contact">
      <p class="contact__name"><span class="contact__first">John</span> Smith</p>
      <p class="contact__title">Managing Director</p>
      <p class="contact__details">
        <span class="contact__label">P:</span> 823-456-7890<br>
        <span class="contact__label">E:</span> info@youremail.com
      </p>
    </div>
  </section>

  <section class="card card--back">
    <div class="back-brand">
      <span class="back-brand__mark"></span>
      <span class="back-brand__name">Varen Inspections</span>
    </div>
    <p class="website">www.webname.com</p>
  </section>
</body>
</html>
```